Used Semi Truck Website Redesign

We are redoing the website backend and would like to also do a front end redesign. I would like a Mobile and Desktop mockup for each page. The website has more mobile visitors than desktop visitors. Our competitor is http://www.haulwaybazaar.example. We don't want to copy them exactly but we want a site that looks more like that. We need the functionality of that site. One big difference is that we also sell parts and trailers.

We need a redesign for front page, product detail page, search result page, content page. It is very important that the site is very easy to use on mobile devices. Our target audience is Truck drivers.

Feel free to use demo fonts stock images, and icons. We will purchase necessary 3rd party media when a winner is chosen.

Target Market(s)

People who want to buy used trucks.

Coding

Coded - Design and coding required

Number of Pages Required

5+ page

Requirements
Must have
• Mockup for Desktop and Mobile pages.

```html
<!DOCTYPE html>
<html lang="en">
<head>
<meta charset="utf-8">
<title>Haulway Bazaar – Trucks and trailers for sale</title>
<link href="https://fonts.googleapis.com/css2?family=Roboto:wght@300;400;500;700&display=swap" rel="stylesheet">
<style>
:root{
  --red:#f2161e;
  --red-dark:#d50f17;
  --ink:#1d1e28;
  --text:#222;
  --muted:#666;
  --line:#e3e3e8;
  --page:#f0f0f4;
  --white:#fff;
  --circle:#ededed;
}
*{box-sizing:border-box;margin:0;padding:0}
html,body{width:1200px;height:2521px;overflow:hidden}
body{position:relative;font-family:'Roboto',sans-serif;color:var(--text);font-size:12px;background:var(--white)}
a{color:inherit;text-decoration:none}

/* hero */
.hero{position:absolute;left:0;top:0;width:1200px;height:249px;background:linear-gradient(180deg,#2b2c37 0%,#383a47 45%,#1f2029 100%)}
.hero-photo{position:absolute;inset:52px 0 0 0;background:linear-gradient(90deg,rgba(20,20,28,.55),rgba(60,60,72,.35) 50%,rgba(20,20,28,.6))}
.topbar{position:absolute;left:0;top:0;width:1200px;height:52px;background:var(--ink)}
.logo{position:absolute;left:89px;top:14px;font-size:19px;font-weight:500;color:var(--white);letter-spacing:.5px}
.nav{position:absolute;left:444px;top:19px;display:flex;font-size:12.5px;color:#c9c9d2}
.nav a{margin-right:22px}
.nav a.active{color:var(--white);position:relative}
.nav a.active::before{content:"";position:absolute;left:0;right:0;top:-19px;height:3px;background:var(--white)}
.nav .sep{width:1px;height:14px;background:#555;margin:1px 22px 0 0}
.social{position:absolute;right:89px;top:19px;display:flex;gap:18px}
.social span{width:12px;height:12px;border-radius:50%;background:#fff}
.hero-title{position:absolute;left:0;width:1200px;top:108px;text-align:center;color:var(--white);font-size:22px;font-weight:300}
.hero-title b{font-weight:500}
.hero-tabs{position:absolute;left:482px;top:151px;display:flex;gap:10px}
.hero-tabs a{height:37px;width:73px;display:flex;align-items:center;justify-content:center;background:rgba(255,255,255,.14);color:var(--white);font-size:12.5px}
.hero-tabs a.on{background:var(--red)}

/* search bar */
.search{position:absolute;left:0;top:249px;width:1200px;height:62px;background:var(--red);display:flex;color:var(--white);font-size:13px}
.field{height:62px;display:flex;align-items:center;justify-content:space-between;padding:0 22px;border-right:1px solid rgba(255,255,255,.3)}
.field svg{width:9px;height:6px}
.f1{margin-left:65px;width:212px;padding-left:24px}
.f2{width:214px}.f3{width:213px}.f4{width:141px}.f5{width:212px;border-right:0}
.search-btn{width:54px;height:62px;background:var(--red-dark);display:flex;align-items:center;justify-content:center}

/* main */
.main-bg{position:absolute;left:0;top:311px;width:753px;height:1886px;background:var(--page)}
.card{position:absolute;left:89px;width:627px;height:360px;background:var(--white);padding:26px 0 0 26px}
.card h2{font-size:19px;font-weight:400;color:var(--text)}
.card h2 small{font-size:11.5px;color:var(--muted)}
.rule{width:42px;height:2px;background:var(--line);margin:14px 0 0}
.card-body{position:absolute;left:26px;top:88px;right:26px;display:flex}
.types{width:304px;list-style:none}
.types li{height:62px;display:flex;align-items:center;gap:17px;font-size:12.5px;color:var(--muted)}
.types li.on{color:var(--text);font-weight:500}
.ico{width:48px;height:48px;border-radius:50%;background:var(--circle);display:flex;align-items:center;justify-content:center}
.on .ico{background:var(--red)}
.ico svg{width:22px;height:14px}
.links{border-left:1px solid var(--line);padding-left:25px;height:230px}
.links ul{list-style:none;margin-top:-1px}
.links li{height:25px;font-size:11.5px;color:#444}
.btn-dark{display:inline-flex;align-items:center;justify-content:center;width:178px;height:32px;background:var(--ink);color:var(--white);font-size:11.5px;font-weight:500;margin-top:10px}
.btn-dark.red{background:var(--red)}

.featured{position:absolute;left:89px;top:1880px;width:627px}
.featured h2{font-size:19px;font-weight:400;margin-top:6px}
.featured .more{position:absolute;right:0;top:0;width:178px;height:32px;border:1px solid #ccc;background:#f6f6f8;display:flex;align-items:center;justify-content:center;font-size:11.5px;color:#555}
.ads{position:absolute;top:63px;left:0;display:flex;gap:3px}
.ad{width:207px;height:202px;position:relative;color:var(--white)}
.ad .img{position:absolute;inset:0}
.ad .meta{position:absolute;left:18px;right:16px;bottom:16px;font-size:11px}
.ad .meta b{display:flex;justify-content:space-between;font-size:12.5px;font-weight:500;margin-top:3px}

/* sidebar */
.box{position:absolute;left:793px;width:318px;background:var(--white);border:1px solid #e6e6ea;padding:26px 24px 0 24px}
.box h3{font-size:19px;font-weight:400}
.input{display:flex;align-items:center;gap:8px;height:40px;border-bottom:1px solid var(--line);font-size:11px;color:#555;margin-top:14px}
.input svg{width:8px;height:10px}
.box h4{font-size:11px;font-weight:500;margin:14px 0 6px}
.grid{display:grid;grid-template-columns:106px 91px 1fr;font-size:11px;color:#333}
.grid span{height:19.5px}
.grid b{font-weight:700}
.box p{font-size:11px;line-height:19px;color:#444;margin-top:18px}
.btn-red{display:inline-flex;align-items:center;justify-content:center;width:104px;height:37px;background:var(--red);color:var(--white);font-size:12px;font-weight:500;margin-top:12px}
.map{position:absolute;left:24px;top:191px;width:271px;height:155px;background:radial-gradient(ellipse at 50% 45%,#d6d6dc,#ececef 70%,transparent 72%)}
.pin{position:absolute;left:160px;top:24px;width:20px;height:26px}
.banner{position:absolute;left:793px;top:1429px;width:318px;height:171px;background:linear-gradient(180deg,#2a2b33,#3b3c45 60%,#26272e);display:flex;align-items:center;justify-content:center;color:var(--white);font-size:19px;font-weight:500}

/* footer */
.footer{position:absolute;left:0;top:2197px;width:1200px;height:279px;background:var(--ink);color:#c9c9d1}
.to-top{position:absolute;left:1135px;top:-20px;width:40px;height:40px;border-radius:50%;background:var(--red);display:flex;align-items:center;justify-content:center}
.col{position:absolute;top:52px}
.col h5{font-size:14px;font-weight:500;color:var(--white)}
.col .rule{background:var(--red);width:24px;margin-top:9px}
.post{font-size:11px;line-height:18px;width:314px;margin-top:16px;padding:0 0 12px 14px;border-bottom:1px solid #35363f;position:relative}
.post::before{content:"";position:absolute;left:0;top:6px;width:6px;height:6px;border-radius:50%;background:#c9c9d1}
.post + .post{border-bottom:0}
.post b{display:block;color:var(--white);font-weight:500;margin-top:3px}
.post .rt{display:flex;align-items:center;gap:6px;color:var(--white);font-weight:500;margin-top:3px}
.res{display:grid;grid-template-columns:133px 1fr;font-size:11px;margin-top:16px}
.res span{height:29px}
.bottom{position:absolute;left:0;top:2476px;width:1200px;height:45px;background:var(--red);color:var(--white);font-size:11px;display:flex;align-items:center;padding:0 89px}
.bottom nav{margin-left:auto;display:flex;gap:28px}
</style>
</head>
<body>

<header class="hero">
  <div class="hero-photo" role="img" aria-label="Photo of parked trucks in a dark depot"></div>
  <div class="topbar">
    <div class="logo">Haulway Bazaar</div>
    <nav class="nav">
      <a class="active">Login</a><a>Register</a><span class="sep"></span><a>Find a dealer</a><a>Dealer Login</a>
    </nav>
    <div class="social" aria-label="Social links"><span></span><span></span><span></span><span></span><span></span></div>
  </div>
  <div class="hero-title"><b>256,140</b> trucks and trailers for sale</div>
  <div class="hero-tabs"><a>Find</a><a class="on">Sell</a><a>Research</a></div>
</header>

<form class="search">
  <div class="field f1">Keywords</div>
  <div class="field f2">Select a class <svg viewBox="0 0 9 6"><path d="M1 1l3.5 3.5L8 1" stroke="#fff" stroke-width="1.4" fill="none"/></svg></div>
  <div class="field f3">Select a category <svg viewBox="0 0 9 6"><path d="M1 1l3.5 3.5L8 1" stroke="#fff" stroke-width="1.4" fill="none"/></svg></div>
  <div class="field f4">Zip code</div>
  <div class="field f5">Any Distance <svg viewBox="0 0 9 6"><path d="M1 1l3.5 3.5L8 1" stroke="#fff" stroke-width="1.4" fill="none"/></svg></div>
  <div class="search-btn"><svg width="18" height="18" viewBox="0 0 18 18"><circle cx="7.5" cy="7.5" r="5.5" stroke="#fff" stroke-width="1.8" fill="none"/><path d="M11.5 11.5l5 5" stroke="#fff" stroke-width="1.8"/></svg></div>
</form>

<div class="main-bg"></div>

<svg width="0" height="0" style="position:absolute">
  <symbol id="truck" viewBox="0 0 22 14"><path d="M0 2h12v8H0zM13 5h5l3 3v2h-8z" fill="currentColor"/><circle cx="4" cy="11.5" r="2" fill="currentColor"/><circle cx="17" cy="11.5" r="2" fill="currentColor"/></symbol>
</svg>

<section class="card" style="top:343px">
  <h2>Find Heavy Duty Trucks For Sale <small>(What Type Heavy Duty Truck do you need?)</small></h2>
  <div class="rule"></div>
  <div class="card-body">
    <ul class="types">
      <li><span class="ico"><svg style="color:#333"><use href="#truck"/></svg></span>Conventional Sleeper Truck</li>
      <li class="on"><span class="ico"><svg style="color:#fff"><use href="#truck"/></svg></span>Dump Truck</li>
      <li><span class="ico"><svg style="color:#333"><use href="#truck"/></svg></span>Conventional Day Cab</li>
      <li><span class="ico"><svg style="color:#333"><use href="#truck"/></svg></span>Wrecker Tow Truck</li>
    </ul>
    <div class="links">
      <ul><li>Cab-Chassis</li><li>Flatbed-Truck</li><li>Box Truck-Straight Truck</li><li>Day Cab</li><li>Tractor</li><li>Crane Truck</li><li>Bucket Truck - Boom Truck</li></ul>
      <a class="btn-dark">View more in this category</a>
    </div>
  </div>
</section>

<section class="card" style="top:726px">
  <h2>Find Medium Duty Trucks For Sale <small>(What type of medium duty truck do you need?)</small></h2>
  <div class="rule"></div>
  <div class="card-body">
    <ul class="types">
      <li><span class="ico"><svg style="color:#333"><use href="#truck"/></svg></span>Box Truck Straight Truck</li>
      <li><span class="ico"><svg style="color:#333"><use href="#truck"/></svg></span>Dump Truck</li>
      <li><span class="ico"><svg style="color:#333"><use href="#truck"/></svg></span>Cab Chassis</li>
      <li><span class="ico"><svg style="color:#333"><use href="#truck"/></svg></span>Flatbed Truck</li>
    </ul>
    <div class="links">
      <ul><li>Rollback Tow Truck</li><li>Utility Truck - Service Truck</li><li>Crew Cab</li><li>Refrigerated Truck</li><li>Wrecker Tow Truck</li><li>Bucket Truck - Boom Truck</li><li>Flatbed</li></ul>
      <a class="btn-dark">View more in this category</a>
    </div>
  </div>
</section>

<section class="card" style="top:1108px">
  <h2>Find Light Duty Trucks For Sale <small>(What Type of Light Duty Truck do you need?)</small></h2>
  <div class="rule"></div>
  <div class="card-body">
    <ul class="types">
      <li><span class="ico"><svg style="color:#333"><use href="#truck"/></svg></span>Utility Truck Service Truck</li>
      <li><span class="ico"><svg style="color:#333"><use href="#truck"/></svg></span>Pickup Truck</li>
      <li><span class="ico"><svg style="color:#333"><use href="#truck"/></svg></span>Box Truck Straight Truck</li>
      <li><span class="ico"><svg style="color:#333"><use href="#truck"/></svg></span>Cargo Van</li>
    </ul>
    <div class="links">
      <ul><li>Dump Truck</li><li>Crew Cab</li><li>Flatbed Truck</li><li>Van</li><li>Passenger Van</li><li>Cutaway-Cube Van</li><li>Refrigerated Truck</li></ul>
      <a class="btn-dark red">View more in this category</a>
    </div>
  </div>
</section>

<section class="card" style="top:1492px">
  <h2>Find Truck Trailers For Sale <small>(What Type of Trailer do you need?)</small></h2>
  <div class="rule"></div>
  <div class="card-body">
    <ul class="types">
      <li><span class="ico"><svg style="color:#333"><use href="#truck"/></svg></span>Enclosed Trailer</li>
      <li><span class="ico"><svg style="color:#333"><use href="#truck"/></svg></span>Flatbed Trailer</li>
      <li><span class="ico"><svg style="color:#333"><use href="#truck"/></svg></span>Dr Van Trailer</li>
      <li><span class="ico"><svg style="color:#333"><use href="#truck"/></svg></span>Car Hauler</li>
    </ul>
    <div class="links">
      <ul><li>Rollback Tow Truck</li><li>Utility Truck - Service Truck</li><li>Crew Cab</li><li>Refrigerated Truck</li><li>Wrecker Tow Truck</li><li>Bucket Truck - Boom Truck</li><li>Flatbed</li></ul>
      <a class="btn-dark">View more in this category</a>
    </div>
  </div>
</section>

<section class="featured">
  <h2>Featured Ads</h2>
  <a class="more">View more featured trucks</a>
  <div class="ads">
    <div class="ad"><div class="img" role="img" aria-label="Photo of a vintage blue truck" style="background:linear-gradient(180deg,#3d6f9e,#1e4a78 60%,#1c2430)"></div><div class="meta">2016 model<b><span>Truck type here</span><span>$53.5k</span></b></div></div>
    <div class="ad"><div class="img" role="img" aria-label="Photo of a white semi truck" style="background:linear-gradient(180deg,#8fb0cf,#c9ccd0 55%,#4a4c50)"></div><div class="meta">2013 model<b><span>Truck type here</span><span>$40.1k</span></b></div></div>
    <div class="ad"><div class="img" role="img" aria-label="Photo of a yellow wheel loader at dusk" style="background:linear-gradient(180deg,#6f8fb0,#b59a63 55%,#3b3324)"></div><div class="meta">2015 model<b><span>Truck type here</span><span>$64.1k</span></b></div></div>
  </div>
</section>

<aside>
  <div class="box" style="top:343px;height:314px">
    <h3>Trucks for sale by State</h3>
    <div class="input"><svg viewBox="0 0 8 10"><path d="M4 10S0 5.5 0 3.8A4 4 0 0 1 8 3.8C8 5.5 4 10 4 10z" fill="#888"/></svg>Enter your state here...</div>
    <h4>Or Select from below:</h4>
    <div class="grid">
      <span>Alabama</span><span>Delaware</span><span>Iowa</span>
      <span>Alaska</span><span>Florida</span><span>Kansas</span>
      <span>Arizona</span><span>Georgia</span><span>Kentucky</span>
      <span>Arkansas</span><span>Hawaii</span><span>Lousiana</span>
      <span>California</span><span>Idaho</span><span>Maine</span>
      <span>Colorado</span><span>Illinois</span><span>Maryland</span>
      <span>Connecticut</span><span>Indiana</span><span><b>More</b></span>
    </div>
  </div>

  <div class="box" style="top:681px;height:314px">
    <h3>Trucks for sale by Make</h3>
    <div class="input"><svg viewBox="0 0 8 10"><path d="M0 5h8M0 3h8M0 7h8" stroke="#888"/></svg>Enter make here...</div>
    <h4>Or Select from below:</h4>
    <div class="grid">
      <span>Halden</span><span>Dunmore</span><span>Linden-Vahl</span>
      <span>Roadcrest</span><span>Kestrel</span><span>Orwick</span>
      <span>Marlow</span><span>Bowline</span><span></span>
      <span>Stonefield</span><span>Norrant</span><span></span>
      <span>Ironvale</span><span>Calder</span><span></span>
      <span>Brackton</span><span>Aster</span><span></span>
      <span>Tovik</span><span>Greyhill</span><span></span>
    </div>
  </div>

  <div class="box" style="top:1019px;height:381px">
    <h3>Find a Dealer</h3>
    <p>Find Commercial Truck dealers by name, make and location.</p>
    <a class="btn-red">Find a dealer</a>
    <div class="map" role="img" aria-label="Dotted world map showing dealer locations">
      <svg class="pin" viewBox="0 0 20 26"><path d="M10 26S0 14 0 10a10 10 0 0 1 20 0c0 4-10 16-10 16z" fill="#f2161e"/><circle cx="10" cy="10" r="3.5" fill="#fff"/></svg>
    </div>
  </div>

  <div class="banner">Ad 358x195</div>
</aside>

<footer class="footer">
  <a class="to-top"><svg width="12" height="12" viewBox="0 0 12 12"><path d="M6 11V2M2 6l4-4 4 4" stroke="#fff" stroke-width="1.6" fill="none"/></svg></a>
  <div class="col" style="left:89px">
    <h5>Our Blogs</h5><div class="rule"></div>
    <div class="post">Dictum nullam felis eu pede mollis pretium integer tinci-dunt cras dapibus vivamus elementum semper.<b>10-Dec-2016</b></div>
    <div class="post">Dec dictum felis eu pede mollis pretium integer tincidunt cras dapibus vivamus elementum semper dipsum.<b>10-Dec-2016</b></div>
  </div>
  <div class="col" style="left:469px">
    <h5>Road Feed</h5><div class="rule"></div>
    <div class="post">Nullam dictum felis eu pede mollis pretium integer tinci-dunt cras dapibus vivamus elementum semper.<span class="rt">↻ Reshare</span></div>
    <div class="post">Lorem dictum felis eu pede mollis pretium integer tinci-dunt cras dapibus vivamus elementum sem ipsum.<span class="rt">↻ Reshare</span></div>
  </div>
  <div class="col" style="left:844px">
    <h5>Resource Advertisers</h5><div class="rule"></div>
    <div class="res">
      <span>› Insurance</span><span>› Truck Parts</span>
      <span>› Jobs &amp; Training</span><span>› Steel Buildings</span>
      <span>› Vehicle History</span><span>› Fuel Management</span>
      <span>› Truck Bodies</span><span>› Shipping &amp; Transport</span>
      <span>› Finance/Lease</span><span>› View All</span>
    </div>
  </div>
</footer>

<div class="bottom">
  <span>© Company name here, All Rights Reserved.</span>
  <nav><a>Trucks for sale</a><a>New Arrivals</a><a>Site map</a></nav>
</div>

</body>
</html>
```